Dynamic Business Card for Sports Supplements Company

Hi! I'm looking for an awesome business card to match my existing sports supplement company. I have uploaded my current company logo and screenshot of the front page of my website.

I would like to have something dynamic and interesting and utilize the colors in the website - the reds and purples

The business card should be double sided and focus on a unique eye-catching design on the back and include all the relevant company info.

Most importantly, it should say somewhere: "Sign up on our website for a coupon code."

Target Market(s)

Mostly for women gym goers but it shouldn't be too feminine. It should be in keeping with the website design. It should flow and clearly be connected to it

Industry/Entity Type

Business

Contact Information for Business Card

Lorraine K. Vestal
CEO
LVestal@Quorvanexco.com
www.quorvanexco.com
555.417.3820
P.O. Box 47315
Alder Falls, Westmark 00000

Sign up on our website for a coupon code

Font styles to use
Serif
Sans Serif
Other font styles liked:
• Novecento font family and "Quorvanex" is in AR Destine font

Requirements
Must have
• One side should be a bold Quorvanex logo design. Even just the symbol itself may be o.k. (see attached file)

```html
<!DOCTYPE html>
<html lang="en">
<head>
<meta charset="utf-8">
<title>Quorvanex Business Card</title>
<link href="https://fonts.googleapis.com/css2?family=Saira+Condensed:wght@700;800&family=Open+Sans:wght@300;400;600&display=swap" rel="stylesheet">
<style>
  :root {
    --brand-red: #e8232a;
    --card-white: #ffffff;
    --ink: #3a3a3a;
    --stage: #1c1c1e;
  }
  * { margin: 0; padding: 0; box-sizing: border-box; }
  html, body { width: 1200px; height: 1000px; overflow: hidden; }
  body {
    background: var(--stage);
    font-family: "Open Sans", Arial, sans-serif;
    position: relative;
  }
  .card {
    position: absolute;
    left: 250px;
    width: 700px;
    height: 400px;
    border-radius: 22px;
    overflow: hidden;
  }
  .card--front { top: 60px; background: var(--card-white); }
  .card--back {
    top: 540px;
    background: var(--brand-red);
    display: flex;
    flex-direction: column;
    align-items: center;
    justify-content: center;
    color: var(--card-white);
  }

  .wordmark {
    font-family: "Saira Condensed", "Arial Narrow", sans-serif;
    font-weight: 800;
    text-transform: uppercase;
    letter-spacing: 2px;
    line-height: 1;
  }
  .tagline {
    font-weight: 300;
    letter-spacing: 3px;
    line-height: 1;
  }

  /* front */
  .front-brand { position: absolute; left: 48px; top: 40px; color: var(--brand-red); }
  .front-brand .wordmark { font-size: 68px; }
  .front-brand .tagline { font-size: 21px; margin-top: 2px; padding-left: 4px; }

  .coupon {
    position: absolute; left: 48px; top: 152px;
    width: 440px;
    color: var(--brand-red);
    font-size: 13px; font-weight: 600;
    letter-spacing: 0.6px;
    text-transform: uppercase;
    padding-bottom: 8px;
    border-bottom: 2px solid var(--brand-red);
  }

  .contact-list { position: absolute; left: 48px; top: 198px; list-style: none; }
  .contact-list li {
    display: flex; align-items: center; gap: 10px;
    font-size: 15px; color: var(--ink);
    margin-bottom: 8px;
  }
  .contact-list svg { width: 15px; height: 15px; fill: var(--brand-red); flex: none; }

  .holder { position: absolute; right: 48px; top: 228px; text-align: right; }
  .holder-name {
    font-family: "Saira Condensed", "Arial Narrow", sans-serif;
    font-weight: 700; font-size: 30px;
    color: var(--brand-red);
    text-transform: uppercase; letter-spacing: 1px; line-height: 1;
  }
  .holder-role { font-size: 15px; color: var(--ink); margin-top: 2px; }

  .address {
    position: absolute; right: 48px; top: 306px;
    display: flex; gap: 10px; align-items: flex-start;
    font-size: 15px; color: var(--ink); line-height: 1.4; text-align: right;
  }
  .address svg { width: 13px; height: 13px; fill: var(--brand-red); margin-top: 4px; flex: none; }

  .swoosh { position: absolute; left: 0; bottom: 0; width: 700px; height: 400px; }
  .website {
    position: absolute; left: 150px; bottom: 11px;
    color: var(--card-white); font-size: 15px; letter-spacing: 0.5px;
  }

  /* back */
  .back-brand { text-align: center; }
  .back-mark { display: flex; align-items: center; justify-content: center; gap: 16px; }
  .back-mark .square { width: 34px; height: 34px; background: var(--card-white); }
  .back-brand .wordmark { font-size: 84px; }
  .back-brand .tagline { font-size: 25px; margin-top: 4px; }
</style>
</head>
<body>

<section class="card card--front" aria-label="Business card front">
  <div class="front-brand">
    <div class="wordmark">Quorvanex</div>
    <div class="tagline">your strength companion</div>
  </div>

  <p class="coupon">Sign up on our website for a coupon code</p>

  <ul class="contact-list">
    <li>
      <svg viewBox="0 0 24 24" aria-hidden="true"><path d="M6.6 10.8a15.1 15.1 0 0 0 6.6 6.6l2.2-2.2a1 1 0 0 1 1-.25 11.4 11.4 0 0 0 3.6.57 1 1 0 0 1 1 1V20a1 1 0 0 1-1 1A17 17 0 0 1 3 4a1 1 0 0 1 1-1h3.5a1 1 0 0 1 1 1c0 1.25.2 2.45.57 3.6a1 1 0 0 1-.25 1z"/></svg>
      555.417.3820
    </li>
    <li>
      <svg viewBox="0 0 24 24" aria-hidden="true"><path d="M2 5h20v14H2z M4 7v.5l8 5 8-5V7l-8 5z" fill-rule="evenodd"/></svg>
      LVestal@Quorvanexco.com
    </li>
  </ul>

  <div class="holder">
    <div class="holder-name">Lorraine K. Vestal</div>
    <div class="holder-role">CEO</div>
  </div>

  <div class="address">
    <svg viewBox="0 0 24 24" aria-hidden="true"><path d="M2 11 22 2 13 22l-2-9z"/></svg>
    <span>P.O. Box 47315<br>Alder Falls, Westmark 00000</span>
  </div>

  <svg class="swoosh" viewBox="0 0 700 400" aria-hidden="true">
    <path d="M0 338 L440 358" stroke="#e8232a" stroke-width="3" fill="none"/>
    <path d="M0 352 L120 358 C135 359 140 368 150 370 L520 370 C535 370 545 400 560 400 L0 400 Z" fill="#e8232a"/>
    <rect x="650" y="370" width="60" height="30" rx="12" fill="#e8232a"/>
  </svg>
  <div class="website">www.quorvanexco.com</div>
</section>

<section class="card card--back" aria-label="Business card back">
  <div class="back-brand">
    <div class="back-mark">
      <span class="square" aria-hidden="true"></span>
      <span class="wordmark">Quorvanex</span>
    </div>
    <div class="tagline">your strength companion</div>
  </div>
</section>

</body>
</html>
```